Gobal construction supply company needs new business card design

I need a business card design for my global supply company using an existing logo. i will be looking to print these on rounded corner cards with the black background version of my logo on the back. on the front white background, my logo again and my simple details.

```html
<!DOCTYPE html>
<html lang="en">
<head>
<meta charset="utf-8">
<title>Meridian Supply Group – Business Cards</title>
<link rel="stylesheet" href="https://fonts.googleapis.com/css2?family=Roboto:wght@400;500;700&display=swap">
<style>
  :root {
    --backdrop: #c6c6c6;
    --card-dark: #1c1c1c;
    --card-light: #f1f1f1;
    --accent-red: #e00000;
    --ink-black: #0c0c0c;
    --ink-grey: #4a4a4a;
    --white: #ffffff;
  }
  * { margin: 0; padding: 0; box-sizing: border-box; }
  html, body {
    width: 1200px; height: 960px; overflow: hidden;
    background: var(--backdrop);
    font-family: "Roboto", Arial, sans-serif;
  }
  .canvas { position: relative; width: 1200px; height: 960px; }

  .card {
    position: absolute; left: 300px; width: 600px; height: 344px;
    border-radius: 20px; overflow: hidden;
  }
  .card--back { top: 122px; background: var(--card-dark); }
  .card--front { top: 495px; background: var(--card-light); }

  .wordmark {
    position: absolute; left: 43px; top: 92px; width: 230px;
    display: flex; align-items: center; gap: 10px;
    font-weight: 700; font-size: 18px; letter-spacing: 0.3px;
    text-transform: uppercase; white-space: nowrap;
  }
  .wordmark__dot { width: 16px; height: 16px; background: var(--accent-red); flex: none; }
  .card--back .wordmark { color: var(--white); }
  .card--front .wordmark { color: var(--ink-black); }

  .web-band {
    position: absolute; right: 0; bottom: 0; width: 270px; height: 37px;
    clip-path: polygon(34px 0, 100% 0, 100% 100%, 0 100%);
    display: flex; align-items: center; justify-content: flex-end;
    padding-right: 45px; color: var(--white); font-size: 14px;
  }
  .card--back .web-band { background: var(--accent-red); }
  .card--front .web-band { background: var(--ink-black); }

  .address {
    position: absolute; left: 43px; top: 182px;
    font-size: 14px; line-height: 18px; color: var(--ink-grey);
  }
  .contact-list {
    position: absolute; left: 43px; top: 228px; list-style: none;
    font-size: 14px; color: var(--ink-grey);
  }
  .contact-list li { display: flex; align-items: center; height: 19px; }
  .contact-list svg { width: 14px; height: 14px; margin-right: 9px; fill: var(--ink-black); }

  .person {
    position: absolute; right: 45px; top: 184px; text-align: right;
  }
  .person__name { font-size: 21px; font-weight: 700; color: var(--ink-black); line-height: 24px; }
  .person__title { font-size: 14px; font-weight: 500; color: var(--accent-red); text-transform: uppercase; }
</style>
</head>
<body>
<main class="canvas">

  <section class="card card--back" aria-label="Card back">
    <div class="wordmark"><span class="wordmark__dot"></span>Meridian Supply Group</div>
    <div class="web-band">meridiansupply.com</div>
  </section>

  <section class="card card--front" aria-label="Card front">
    <div class="wordmark"><span class="wordmark__dot"></span>Meridian Supply Group</div>

    <address class="address" style="font-style:normal">
      1420 Harbor View Road<br>Portland, Oregon 97205
    </address>

    <ul class="contact-list">
      <li><svg viewBox="0 0 24 24"><path d="M6.6 10.8a15.1 15.1 0 0 0 6.6 6.6l2.2-2.2a1 1 0 0 1 1-.25 11.4 11.4 0 0 0 3.6.6 1 1 0 0 1 1 1V20a1 1 0 0 1-1 1A17 17 0 0 1 3 4a1 1 0 0 1 1-1h3.5a1 1 0 0 1 1 1c0 1.25.2 2.45.6 3.6a1 1 0 0 1-.25 1z"/></svg>503 214 7780</li>
      <li><svg viewBox="0 0 24 24"><path d="M7 1h10a2 2 0 0 1 2 2v18a2 2 0 0 1-2 2H7a2 2 0 0 1-2-2V3a2 2 0 0 1 2-2zm0 3v14h10V4zm5 15.5a1 1 0 1 0 0 2 1 1 0 0 0 0-2z"/></svg>503 891 4426</li>
      <li><svg viewBox="0 0 24 24"><path d="M6 2h10l2 2v5H6zM3 10h18a1 1 0 0 1 1 1v7H2v-7a1 1 0 0 1 1-1zm3 10h12v2H6z"/></svg>503 214 7781</li>
      <li><svg viewBox="0 0 24 24"><path d="M2 5h20v14H2zm2 2v.5l8 5 8-5V7zm0 2.8V17h16V9.8l-8 5z"/></svg>daniel@meridiansupply.com</li>
    </ul>

    <div class="person">
      <div class="person__name">DANIEL HARTLEY</div>
      <div class="person__title">CEO/Founder</div>
    </div>

    <div class="web-band">meridiansupply.com</div>
  </section>

</main>
</body>
</html>
```